Private Investigation Business Card Design

I need a business card for a new private investigation company named Brisk Inquiries. I perform mainly surveillance jobs, vehicle repossessions, document serves etc. The final design should aim for a professional look. The logo has a magnifying glass with stick man arms and legs and is in a running action to show the "Brisk" aspect of the name. If the colour scheme could remain the same as the website www.briskinquiries-demo.com.au with silvers,blacks and a couple electric blue highlights.
Industry/Entity Type
Business
Contact Information for Business Card
Morgan Kellaway
Brisk Inquiries
0487316204
PO Box 58, Carnwell NSW 2291
info@briskinquiries-demo.com.au
www.briskinquiries-demo.com.au
Look and feel

```html
<!DOCTYPE html>
<html lang="en">
<head>
<meta charset="utf-8">
<title>Brisk Inquiries – Business Card</title>
<link href="https://fonts.googleapis.com/css2?family=Open+Sans:wght@400;600&display=swap" rel="stylesheet">
<style>
  :root {
    --stage-top: #2b2b2b;
    --stage-bottom: #050505;
    --card-front: #f3f3f3;
    --card-back-top: #a3a3a3;
    --card-back-bottom: #858585;
    --ink: #1e1e1e;
    --ink-soft: #8a8a8a;
    --brand-grey: #5a5a5a;
    --brand-light: #e6e6e6;
  }
  html, body {
    margin: 0;
    padding: 0;
    width: 1200px;
    height: 900px;
    overflow: hidden;
  }
  body {
    font-family: "Open Sans", sans-serif;
    background: linear-gradient(180deg, var(--stage-top) 0%, #1c1c1c 45%, var(--stage-bottom) 100%);
    position: relative;
  }
  .card {
    position: absolute;
    top: 184px;
    height: 490px;
    border-radius: 12px;
    box-shadow: 0 2px 6px rgba(0,0,0,0.5);
    overflow: hidden;
  }
  .card--front {
    left: 299px;
    width: 301px;
    background: var(--card-front);
    color: var(--ink);
    text-align: center;
  }
  .card--back {
    left: 645px;
    width: 304px;
    background: linear-gradient(180deg, var(--card-back-top) 0%, #9a9a9a 50%, var(--card-back-bottom) 100%);
  }
  .brand-mark {
    position: absolute;
    display: flex;
    align-items: center;
    gap: 10px;
    font-weight: 600;
    white-space: nowrap;
  }
  .card--front .brand-mark {
    top: 238px;
    top: 50px;
    left: 24px;
    font-size: 34px;
    color: var(--brand-grey);
  }
  .brand-dot {
    width: 26px;
    height: 26px;
    border-radius: 50%;
    background: var(--brand-grey);
  }
  .holder {
    position: absolute;
    top: 224px;
    width: 100%;
  }
  .holder__name {
    font-size: 16px;
    font-weight: 600;
    color: var(--ink-soft);
    line-height: 22px;
  }
  .holder__company {
    font-size: 13px;
    line-height: 18px;
  }
  .contact {
    position: absolute;
    top: 301px;
    width: 100%;
    list-style: none;
    margin: 0;
    padding: 0;
    font-size: 13px;
    line-height: 20.5px;
  }
  .contact li {
    display: flex;
    justify-content: center;
    align-items: center;
    gap: 4px;
  }
  .contact svg {
    width: 10px;
    height: 10px;
    fill: #555;
    stroke: #555;
  }
  .address {
    position: absolute;
    top: 399px;
    width: 100%;
    font-size: 13px;
    line-height: 20px;
    font-style: normal;
  }
  .back-artwork {
    position: absolute;
    left: 0;
    top: 16px;
    width: 304px;
    height: 360px;
    background: radial-gradient(ellipse at 50% 35%, rgba(200,200,200,0.55) 0%, rgba(170,170,170,0.25) 45%, rgba(150,150,150,0) 75%);
  }
  .card--back .brand-mark {
    left: 0;
    right: 0;
    justify-content: center;
    top: 388px;
    font-size: 38px;
    color: var(--brand-light);
  }
</style>
</head>
<body>
  <section class="card card--front" aria-label="Card front">
    <div class="brand-mark">
      <span>Brisk Inquiries</span>
    </div>
    <div class="holder">
      <div class="holder__name">Morgan Kellaway</div>
      <div class="holder__company">Brisk Inquiries</div>
    </div>
    <ul class="contact">
      <li>
        <svg viewBox="0 0 10 10" aria-hidden="true"><path stroke="none" d="M1 3 Q1 1 3 1 L7 1 Q9 1 9 3 L8 4 L6.5 3.5 L6.5 2.6 L3.5 2.6 L3.5 3.5 L2 4 Z M2.5 5 L7.5 5 L8.5 9 L1.5 9 Z"/></svg>
        <span>0487316204</span>
      </li>
      <li>
        <svg viewBox="0 0 10 10" aria-hidden="true"><rect x="0.5" y="2" width="9" height="6.5" stroke="none"/><path d="M0.8 2.4 L5 5.6 L9.2 2.4" fill="none" stroke="#f3f3f3" stroke-width="0.9"/></svg>
        <span>info@briskinquiries-demo.com.au</span>
      </li>
      <li>
        <svg viewBox="0 0 10 10" aria-hidden="true"><path d="M4 6 L6 4 M3.2 5 L1.8 6.4 A1.4 1.4 0 0 0 3.6 8.2 L5 6.8 M5 3.2 L6.4 1.8 A1.4 1.4 0 0 1 8.2 3.6 L6.8 5" fill="none" stroke-width="1" stroke-linecap="round"/></svg>
        <span>www.briskinquiries-demo.com.au</span>
      </li>
    </ul>
    <address class="address">PO Box 58, Carnwell<br>NSW 2291</address>
  </section>

  <section class="card card--back" aria-label="Card back">
    <div class="back-artwork" role="img" aria-label="Large faint running brand figure decoration"></div>
    <div class="brand-mark">
      <span>Brisk Inquiries</span>
    </div>
  </section>
</body>
</html>
```